Stationery Design Project

We need, stationary designs for a store of children and juvenile furniture.
we have the logo. also need tags for the furniture with enought space to include description and options , maybe a 4" x 6" tag.

Target Market(s)

Parents of childrens and teens

Industry/Entity Type

Store

```html
<!DOCTYPE html>
<html lang="en">
<head>
<meta charset="utf-8">
<title>Nestwood – Presentation Folder</title>
<link rel="stylesheet" href="https://fonts.googleapis.com/css2?family=Open+Sans:wght@400;600&display=swap">
<style>
  :root {
    --backdrop: #dcdcdc;
    --paper: #ffffff;
    --teal: #56c4d0;
    --teal-soft: #bfe8ed;
    --orange: #f08a2c;
    --grey-text: #7a7a7a;
    --brand-grey: #6e6e70;
  }
  * { box-sizing: border-box; margin: 0; padding: 0; }
  html, body {
    width: 1200px; height: 900px; overflow: hidden;
    background: var(--backdrop);
    font-family: "Open Sans", Arial, sans-serif;
  }
  .folder {
    position: absolute; top: 120px; left: 130px;
    display: flex; gap: 60px;
  }
  .panel {
    position: relative;
    width: 440px; height: 660px;
    background: var(--paper);
    box-shadow: 0 10px 30px rgba(0,0,0,0.18);
    overflow: hidden;
  }
  .decor {
    position: absolute;
    background: linear-gradient(135deg, var(--teal) 0%, var(--teal-soft) 100%);
    border-radius: 0 0 120px 120px;
  }
  .front-cover .decor { top: 90px; left: 0; width: 320px; height: 240px; border-radius: 0 140px 120px 0; }
  .back-cover .decor { top: 30px; right: 0; width: 360px; height: 290px; border-radius: 150px 0 0 140px; }
  .brand {
    position: absolute; right: 24px; bottom: 40px;
    display: flex; align-items: center; gap: 12px;
  }
  .brand-mark { width: 34px; height: 34px; background: var(--teal); }
  .brand-name {
    font-size: 34px; font-weight: 600; letter-spacing: 1px;
    color: var(--brand-grey);
  }
  .contact-list {
    position: absolute; left: 22px; bottom: 28px;
    list-style: none;
    font-size: 8px; line-height: 1.35; color: var(--grey-text);
  }
  .contact-item { display: flex; align-items: center; gap: 9px; margin-top: 10px; }
  .contact-icon { width: 13px; height: 13px; flex: none; }
</style>
</head>
<body>
  <div class="folder">
    <section class="panel front-cover">
      <div class="decor" role="img" aria-label="Large decorative teal cloud outline illustration"></div>
      <div class="brand">
        <span class="brand-mark"></span>
        <span class="brand-name">Nestwood</span>
      </div>
    </section>

    <section class="panel back-cover">
      <div class="decor" role="img" aria-label="Overlapping decorative teal cloud outline illustration"></div>
      <ul class="contact-list">
        <li class="contact-item">
          <svg class="contact-icon" viewBox="0 0 14 14"><circle cx="7" cy="7" r="7" fill="var(--orange)"/><path d="M7 3.2a2.4 2.4 0 0 0-2.4 2.4c0 1.8 2.4 4.6 2.4 4.6s2.4-2.8 2.4-4.6A2.4 2.4 0 0 0 7 3.2z" fill="#fff"/><circle cx="7" cy="5.6" r="0.9" fill="var(--orange)"/></svg>
          <span>Office #, Building Street, City<br>State XXXXX Country</span>
        </li>
        <li class="contact-item">
          <svg class="contact-icon" viewBox="0 0 14 14"><circle cx="7" cy="7" r="7" fill="var(--orange)"/><path d="M4.5 3.8l1.3-.3.8 1.8-.9.7a5 5 0 0 0 2.3 2.3l.7-.9 1.8.8-.3 1.3c-3.2.2-5.9-2.5-5.7-5.7z" fill="#fff"/></svg>
          <span>123 456 7890</span>
        </li>
        <li class="contact-item">
          <svg class="contact-icon" viewBox="0 0 14 14"><circle cx="7" cy="7" r="7" fill="var(--orange)"/><rect x="3.6" y="4.6" width="6.8" height="4.8" fill="#fff"/><path d="M3.6 4.6L7 7.4l3.4-2.8" fill="none" stroke="var(--orange)" stroke-width="0.7"/></svg>
          <span>hello@nestwood.com</span>
        </li>
        <li class="contact-item">
          <svg class="contact-icon" viewBox="0 0 14 14"><circle cx="7" cy="7" r="7" fill="var(--orange)"/><circle cx="7" cy="7" r="3.3" fill="#fff"/><path d="M3.7 7h6.6M7 3.7c-1.6 2.2-1.6 4.4 0 6.6M7 3.7c1.6 2.2 1.6 4.4 0 6.6" fill="none" stroke="var(--orange)" stroke-width="0.6"/></svg>
          <span>www.nestwood.com</span>
        </li>
      </ul>
    </section>
  </div>
</body>
</html>
```